"Harbor Builders" is a residential building company and needs a new business card design and may re

We would like a redesign based on the existing logo, and would like to see a new font as well. We are bespoke home builders who build sustainable energy efficient homes.

Industry/Entity Type

Construction

Contact Information for Business Card

Business card size 40mm x 90mm

Colors

Designer to choose colors to be used in the design.

```html
<!DOCTYPE html>
<html lang="en">
<head>
<meta charset="utf-8">
<title>Harbor Builders – Business Card</title>
<link href="https://fonts.googleapis.com/css2?family=Montserrat:wght@400;500;700;800&display=swap" rel="stylesheet">
<style>
  :root {
    --navy: #22347f;
    --orange: #ee7f2a;
    --orange-deep: #d9691c;
    --ink: #555a63;
    --paper: #ffffff;
    --backdrop: #1c1c1e;
  }
  * { box-sizing: border-box; margin: 0; padding: 0; }
  html, body { width: 1200px; height: 963px; overflow: hidden; }
  body {
    background: var(--backdrop);
    font-family: "Montserrat", sans-serif;
    display: flex; flex-direction: column; align-items: center; justify-content: center;
    gap: 56px;
  }
  .card {
    width: 900px; height: 400px; border-radius: 22px; position: relative;
    box-shadow: 0 18px 40px rgba(0,0,0,.5);
  }
  .card-front { background: var(--paper); }
  .card-back {
    background: linear-gradient(135deg, var(--orange) 0%, var(--orange-deep) 100%);
    display: flex; align-items: center; justify-content: center;
  }
  .brand { display: flex; align-items: center; gap: 16px; }
  .brand-mark { width: 34px; height: 34px; }
  .brand-name {
    font-weight: 800; font-size: 40px; letter-spacing: 3px; text-transform: uppercase;
  }
  .card-front .brand { position: absolute; right: 70px; top: 128px; }
  .card-front .brand-mark { background: var(--orange); }
  .card-front .brand-name { color: var(--navy); }
  .card-back .brand-mark { background: #f1f1f1; }
  .card-back .brand-name { color: #f1f1f1; font-size: 52px; }

  .person { position: absolute; left: 60px; top: 70px; }
  .person-name { color: var(--navy); font-weight: 800; font-size: 28px; text-transform: uppercase; letter-spacing: .5px; }
  .person-role { color: var(--ink); font-size: 19px; margin-top: 4px; }
  .rule { width: 28px; height: 3px; background: var(--orange); margin: 18px 0 20px; }
  .contact-list { list-style: none; }
  .contact-list li { display: flex; align-items: center; gap: 12px; color: var(--ink); font-size: 18px; line-height: 32px; }
  .contact-list svg { width: 16px; height: 16px; fill: var(--orange); flex: none; }

  .office { position: absolute; right: 70px; bottom: 50px; text-align: right; color: var(--ink); font-size: 17px; line-height: 28px; }
  .office .label { color: var(--navy); font-weight: 500; }
</style>
</head>
<body>
  <section class="card card-front">
    <div class="person">
      <h1 class="person-name">Daniel Marlowe</h1>
      <p class="person-role">Founder</p>
      <div class="rule"></div>
      <ul class="contact-list">
        <li><svg viewBox="0 0 16 16"><path d="M3 1h3l1.5 4-2 1.3a9 9 0 0 0 4.2 4.2L11 8.5l4 1.5v3a2 2 0 0 1-2 2A12 12 0 0 1 1 3a2 2 0 0 1 2-2z"/></svg>0400 555 018</li>
        <li><svg viewBox="0 0 16 16"><path d="M1 3h14v10H1z M1 3l7 6 7-6" fill="none" stroke="#ee7f2a" stroke-width="1.8"/></svg>daniel@harborbuilders.com.au</li>
        <li><svg viewBox="0 0 16 16"><circle cx="8" cy="8" r="7" fill="none" stroke="#ee7f2a" stroke-width="1.6"/><path d="M1 8h14M8 1c-3 3.5-3 10.5 0 14M8 1c3 3.5 3 10.5 0 14" fill="none" stroke="#ee7f2a" stroke-width="1.3"/></svg>www.harborbuilders.com.au</li>
      </ul>
    </div>
    <div class="brand">
      <span class="brand-mark"></span>
      <span class="brand-name">Harbor Builders</span>
    </div>
    <address class="office" style="font-style:normal">
      PO Box 2187 Northgate<br>
      LPO Ridgeway WA 6100<br>
      <span class="label">Reg:</span> -40318 | <span class="label">ABN:</span> 52 604 219 837
    </address>
  </section>

  <section class="card card-back">
    <div class="brand">
      <span class="brand-mark"></span>
      <span class="brand-name">Harbor Builders</span>
    </div>
  </section>
</body>
</html>
```